we can communicate on this, but i want to follow the approach we took on Pellew|Marsh & Quinlan but i feel the card front needs the black background and the platinum and gold logo. The back? I am open. we can use the same info from PM&Q. Velmont Arc is an enhanced equity investment fund - basically a very exclusive boutique hedge fund that uses only stock options. very advanced things. hope you are interested

Contact Information for Business Card

Dr. Lewis T. Brennick, CFA
Scientifique de fusée financière
701.555.0143
LTBquant47@mailvantor.com

4718 Willow Creek Bend W.
West Fargo, ND 58078

No web site

Colors

Designer to choose colors to be used in the design.

Requirements
Nice to have
• I tend to prefer the most visible applications of the logo to include logo and name, the logo version with a black background and the gold and platinum components separated by the black. I see this working well for a single side (logo and name - this is card front to me).
• I am fairly open to other treatments on the reverse side with the data. To me, it makes sense to have a different color rendition of the logo on the reverse and it may be a muted black tone on tone or an oversized portion that would have spot UV. Or, the reverse may play with colors and layout
Should not have
• Other colors = no no
• Decorative font

```html
<!DOCTYPE html>
<html lang="en">
<head>
<meta charset="utf-8">
<title>Velmont Arc – Business Card</title>
<link href="https://fonts.googleapis.com/css2?family=Montserrat:wght@400;600;700&family=Open+Sans:wght@400&display=swap" rel="stylesheet">
<style>
  :root {
    --backdrop: #5b5b5b;
    --card: #050505;
    --gold: #b9a14a;
    --platinum: #d6d6d8;
    --white: #f4f4f4;
    --rule: #4a4a4a;
  }
  * { margin: 0; padding: 0; box-sizing: border-box; }
  html, body {
    width: 1200px; height: 985px; overflow: hidden;
    background: var(--backdrop);
  }
  .sheet { position: relative; width: 1200px; height: 985px; }
  .card {
    position: absolute; left: 250px; width: 700px; height: 400px;
    background: var(--card);
    box-shadow: 0 10px 28px rgba(0,0,0,0.45);
  }
  .card--front { top: 55px; }
  .card--back { top: 530px; }

  /* Front */
  .brand {
    position: absolute; inset: 0;
    display: flex; flex-direction: column; align-items: center; justify-content: center;
    gap: 18px;
  }
  .brand__disc {
    width: 92px; height: 92px; border-radius: 50%;
    background: var(--gold);
  }
  .brand__name {
    font-family: "Montserrat", sans-serif; font-weight: 700;
    font-size: 50px; letter-spacing: 1px; color: var(--white);
    text-transform: uppercase;
  }

  /* Back */
  .back-brand {
    position: absolute; top: 58px; right: 60px;
    display: flex; align-items: center; gap: 14px;
  }
  .back-brand__disc {
    width: 26px; height: 26px; border-radius: 50%; background: var(--platinum);
  }
  .back-brand__name {
    font-family: "Montserrat", sans-serif; font-weight: 700;
    font-size: 24px; color: var(--white); text-transform: uppercase; letter-spacing: 1px;
  }
  .holder { position: absolute; left: 90px; top: 148px; }
  .holder__name {
    font-family: "Montserrat", sans-serif; font-weight: 600;
    font-size: 26px; color: var(--gold); text-transform: uppercase; letter-spacing: 0.5px;
  }
  .holder__title {
    font-family: "Open Sans", sans-serif; font-size: 17px; color: var(--white);
    margin-top: 2px; letter-spacing: 0.6px;
  }
  .divider {
    position: absolute; left: 78px; right: 72px; top: 218px;
    height: 1px; background: var(--rule);
  }
  .contact {
    position: absolute; left: 80px; top: 232px;
    font-family: "Open Sans", sans-serif; font-size: 17px; color: var(--white);
    list-style: none; letter-spacing: 0.8px;
  }
  .contact__item { display: flex; align-items: center; gap: 16px; height: 30px; }
  .contact__icon { width: 16px; height: 16px; flex: none; }
  .address {
    position: absolute; right: 72px; bottom: 32px; text-align: right;
    font-family: "Open Sans", sans-serif; font-size: 17px; line-height: 1.55;
    color: var(--white); letter-spacing: 0.8px; font-style: normal;
  }
</style>
</head>
<body>
<main class="sheet">
  <section class="card card--front" aria-label="Card front">
    <div class="brand">
      <span class="brand__disc"></span>
      <span class="brand__name">Velmont Arc</span>
    </div>
  </section>

  <section class="card card--back" aria-label="Card back">
    <div class="back-brand">
      <span class="back-brand__disc"></span>
      <span class="back-brand__name">Velmont Arc</span>
    </div>

    <div class="holder">
      <h1 class="holder__name">Dr. Lewis T. Brennick, CFA</h1>
      <p class="holder__title">Scientifique des Fusées Financières</p>
    </div>

    <div class="divider"></div>

    <ul class="contact">
      <li class="contact__item">
        <svg class="contact__icon" viewBox="0 0 24 24" aria-hidden="true">
          <path fill="#b9a14a" d="M6.6 10.8a15.1 15.1 0 0 0 6.6 6.6l2.2-2.2a1 1 0 0 1 1-.25 11.4 11.4 0 0 0 3.6.57 1 1 0 0 1 1 1V20a1 1 0 0 1-1 1A17 17 0 0 1 3 4a1 1 0 0 1 1-1h3.5a1 1 0 0 1 1 1c0 1.25.2 2.45.57 3.57a1 1 0 0 1-.25 1z"/>
        </svg>
        <span>701.555.0143</span>
      </li>
      <li class="contact__item">
        <svg class="contact__icon" viewBox="0 0 24 24" aria-hidden="true">
          <rect x="2" y="5" width="20" height="14" rx="1.5" fill="#b9a14a"/>
          <path d="M3 6.5l9 6.5 9-6.5" fill="none" stroke="#050505" stroke-width="1.8"/>
        </svg>
        <span>LTBquant47@mailvantor.com</span>
      </li>
    </ul>

    <address class="address">
      4718 Willow Creek Bend W.<br>
      West Fargo, ND 58078
    </address>
  </section>
</main>
</body>
</html>
```